Valdane Companies Business Card Design

We need a new business card for our Private Equity Real Estate Development firm, “Valdane” and our EB-5 regional center “Thornmere Regional Center” on one card. We prefer a design that is simple, elegant, and represents the luxury products we design and build as well as the financial security and stability our successful history has produced. We are an industry leader in our field and 3rd generation family business that has evolved into an institutional quality investment platform. Considered design size is standard business card dimensions (3.5 x 2 inches with an additional 1/8 inch space for design elements or backgrounds that extend beyond the finished size of your piece.

Target Market(s)

• High net worth individuals
• Highly skilled technical workers and physicians in the US seeking investment-based immigration opportunities
• Sophisticated private equity investors
• Intermediary partners include domestic attorneys and investment brokers, as well as international agent networks
• US real estate developers

Industry/Entity Type

Finance

Contact Information for Business Card

(Providing placeholder info for personal information, please design for longer character spaces, longer names and addresses etc..)
• Logo for Valdane
• Logo for Thornmere Regional Center
• Full name: Marcus Valdane
• Job title: CEO
• Email address: mvaldane@valdanecompanies.com
• Cell phone number: +1.555.314.2287
• Office number +1.555.628.4410
• Office address: Larkfield Court 5, 4817 Vista Orilla, Brackenfield, CA.
• Website: www.valdanecompanies.com

Font styles to use
Serif
Sans Serif

Colors
ec1f27
ffffff
000000

Requirements
Must have
• • Logo for Valdane
• • Logo for Thornmere Regional Center
• - Use rounded corners
• (See .ai file included for logos)
Nice to have
• • Simple, elegant design
• • Aesthetically compatible with our website design (www.valdanecompanies.com)
• • Color palette including but not limited to white, black, and red (as per logos)
Should not have
• - Not too much red color
• - Do not stack both logos on top of each other

```html
<!DOCTYPE html>
<html lang="en">
<head>
<meta charset="utf-8">
<title>Valdane Companies Business Card</title>
<link rel="stylesheet" href="https://fonts.googleapis.com/css2?family=Crimson+Pro:wght@400;600;700&family=Nunito+Sans:wght@400;600&display=swap">
<style>
  :root {
    --red: #b5132a;
    --ink: #111111;
    --black: #000000;
    --white: #ffffff;
    --rule: #9a9a9a;
    --mark-grey: #4a4a4a;
    --backdrop: #3a3b3d;
    --serif: "Crimson Pro", Georgia, serif;
    --sans: "Nunito Sans", Arial, sans-serif;
  }
  * { box-sizing: border-box; margin: 0; padding: 0; }
  html, body { width: 1200px; height: 900px; overflow: hidden; }
  body {
    background: var(--backdrop);
    position: relative;
    font-family: var(--sans);
  }
  .card {
    position: absolute;
    left: 285px;
    width: 630px;
    height: 360px;
    border-radius: 28px;
    overflow: hidden;
  }
  /* Back side */
  .card-back { top: 60px; background: var(--black); }
  .back-brand {
    position: absolute;
    inset: 0;
    display: flex;
    align-items: center;
    justify-content: center;
    gap: 18px;
  }
  .back-square {
    width: 34px;
    height: 34px;
    background: var(--mark-grey);
  }
  .back-name {
    font-family: var(--serif);
    font-weight: 600;
    font-size: 58px;
    letter-spacing: 4px;
    color: var(--mark-grey);
    text-transform: uppercase;
  }
  /* Front side */
  .card-front { top: 480px; background: var(--white); }
  .front-band {
    position: absolute;
    left: 0; right: 0; bottom: 0;
    height: 6px;
    background: var(--red);
  }
  .center-brand {
    position: absolute;
    left: 44px;
    top: 128px;
    width: 190px;
    font-family: var(--serif);
    font-weight: 700;
    font-size: 26px;
    line-height: 1.05;
    color: var(--red);
    text-transform: uppercase;
    letter-spacing: 1px;
  }
  .contact {
    position: absolute;
    left: 262px;
    top: 70px;
    width: 330px;
  }
  .contact-top-rule { height: 1px; background: var(--rule); margin-bottom: 22px; }
  .person-name {
    font-family: var(--serif);
    font-weight: 700;
    font-size: 30px;
    line-height: 1;
    color: var(--ink);
  }
  .person-title {
    font-family: var(--serif);
    font-weight: 600;
    font-size: 18px;
    color: var(--red);
    margin-top: 4px;
  }
  .contact-mid-rule { height: 1px; background: var(--rule); margin: 8px 0 10px; }
  .contact-list {
    display: grid;
    grid-template-columns: 64px 12px 1fr;
    row-gap: 3px;
    font-size: 14px;
    line-height: 1.25;
  }
  .contact-label { color: var(--red); }
  .contact-colon { color: var(--ink); }
  .contact-value { color: var(--ink); }
</style>
</head>
<body>
  <section class="card card-back" aria-label="Business card back">
    <div class="back-brand">
      <span class="back-square"></span>
      <span class="back-name">Valdane</span>
    </div>
  </section>

  <section class="card card-front" aria-label="Business card front">
    <div class="center-brand">Thornmere<br>Regional Center</div>

    <div class="contact">
      <div class="contact-top-rule"></div>
      <h1 class="person-name">Marcus Valdane</h1>
      <p class="person-title">CEO</p>
      <div class="contact-mid-rule"></div>
      <div class="contact-list">
        <span class="contact-label">Office</span><span class="contact-colon">:</span><span class="contact-value">+1.555.628.4410</span>
        <span class="contact-label">Cell</span><span class="contact-colon">:</span><span class="contact-value">+1.555.314.2287</span>
        <span class="contact-label">Email</span><span class="contact-colon">:</span><span class="contact-value">mvaldane@valdanecompanies.com</span>
        <span class="contact-label">Web</span><span class="contact-colon">:</span><span class="contact-value">www.valdanecompanies.com</span>
        <span class="contact-label">Address</span><span class="contact-colon">:</span><span class="contact-value">Larkfield Court 5, 4817 Vista Orilla,<br>Brackenfield, CA.</span>
      </div>
    </div>

    <div class="front-band"></div>
  </section>
</body>
</html>
```